Stonebridge Building and Projects business cards

A business card with watermark background (construction work)

Company logo attached

Home improvement projects
House renovations
Bathroom and kitchen renovations
House extensions
New builds and granny flats

Director Omar Haddani
(Phone number)
omar@sbpbuilding.com.au
(Instagram logo) sbp_building

```html
<!DOCTYPE html>
<html lang="en">
<head>
<meta charset="utf-8">
<title>Stonebridge Building and Projects – Business Cards</title>
<link href="https://fonts.googleapis.com/css2?family=Roboto:wght@400;500;700&display=swap" rel="stylesheet">
<style>
  :root {
    --brand-blue: #1b78c2;
    --ink: #3a3d42;
    --slate: #3b3f45;
    --card: #f4f5f6;
    --page: #e6e7e9;
    --white: #ffffff;
  }
  * { box-sizing: border-box; margin: 0; padding: 0; }
  html, body { width: 1200px; height: 1050px; overflow: hidden; }
  body {
    background: var(--page);
    font-family: "Roboto", Arial, sans-serif;
    position: relative;
  }
  .card {
    position: absolute;
    left: 250px;
    width: 700px;
    height: 400px;
    background: var(--card);
    border-radius: 26px;
    overflow: hidden;
    box-shadow: 0 6px 18px rgba(0,0,0,0.15);
  }
  .card--front { top: 95px; }
  .card--back { top: 555px; }

  .wordmark {
    position: absolute;
    display: flex;
    align-items: center;
    gap: 12px;
    color: var(--brand-blue);
    font-weight: 700;
    font-size: 26px;
    line-height: 1.15;
    width: 300px;
  }
  .wordmark__square {
    width: 22px; height: 22px;
    background: var(--brand-blue);
    flex: none;
  }
  .card--front .wordmark { left: 44px; top: 150px; }
  .card--back .wordmark { left: 44px; top: 140px; }

  .services {
    position: absolute;
    left: 370px;
    top: 70px;
    list-style: none;
    color: var(--ink);
    font-size: 19px;
    line-height: 1.45;
  }
  .services li { display: flex; gap: 12px; align-items: flex-start; }
  .services svg { flex: none; margin-top: 7px; }

  .social-band {
    position: absolute;
    right: 0; bottom: 68px;
    width: 360px; height: 52px;
    background: var(--brand-blue);
    border-radius: 26px 0 0 0;
    color: var(--white);
    font-size: 18px;
    display: flex; align-items: center; gap: 12px;
    padding-left: 44px;
  }
  .social-band__dot {
    width: 14px; height: 14px; border-radius: 50%;
    border: 2px solid var(--white);
  }
  .social-band__edge {
    position: absolute;
    right: 0; bottom: 58px;
    width: 360px; height: 10px;
    background: var(--slate);
  }

  .wave { position: absolute; inset: 0; }
  .person {
    position: absolute;
    right: 48px; top: 44px;
    text-align: right;
  }
  .person__name { color: var(--brand-blue); font-weight: 700; font-size: 24px; }
  .person__role { color: var(--ink); font-size: 15px; margin-top: 2px; }

  .contacts {
    position: absolute;
    right: 32px; top: 200px;
    list-style: none;
    color: var(--white);
    font-size: 16px;
    line-height: 24px;
    text-align: right;
  }
  .contacts li { display: flex; justify-content: flex-end; align-items: center; gap: 12px; }
  .contacts svg { flex: none; }
</style>
</head>
<body>

<section class="card card--front">
  <div class="wordmark">
    <span class="wordmark__square"></span>
    <span>Stonebridge Building and Projects</span>
  </div>

  <ul class="services">
    <li><svg width="10" height="10" viewBox="0 0 10 10"><g fill="#1b78c2"><rect width="4" height="4"/><rect x="6" width="4" height="4"/><rect y="6" width="4" height="4"/><rect x="6" y="6" width="4" height="4"/></g></svg>Home improvement projects</li>
    <li><svg width="10" height="10" viewBox="0 0 10 10"><g fill="#1b78c2"><rect width="4" height="4"/><rect x="6" width="4" height="4"/><rect y="6" width="4" height="4"/><rect x="6" y="6" width="4" height="4"/></g></svg>House renovations</li>
    <li><svg width="10" height="10" viewBox="0 0 10 10"><g fill="#1b78c2"><rect width="4" height="4"/><rect x="6" width="4" height="4"/><rect y="6" width="4" height="4"/><rect x="6" y="6" width="4" height="4"/></g></svg>Bathroom and kitchen<br>renovations</li>
    <li><svg width="10" height="10" viewBox="0 0 10 10"><g fill="#1b78c2"><rect width="4" height="4"/><rect x="6" width="4" height="4"/><rect y="6" width="4" height="4"/><rect x="6" y="6" width="4" height="4"/></g></svg>House extensions</li>
    <li><svg width="10" height="10" viewBox="0 0 10 10"><g fill="#1b78c2"><rect width="4" height="4"/><rect x="6" width="4" height="4"/><rect y="6" width="4" height="4"/><rect x="6" y="6" width="4" height="4"/></g></svg>New builds and granny flats</li>
  </ul>

  <div class="social-band">
    <span class="social-band__dot"></span>
    <span>sbp_building</span>
  </div>
  <div class="social-band__edge"></div>
</section>

<section class="card card--back">
  <svg class="wave" viewBox="0 0 700 400" preserveAspectRatio="none">
    <path class="wave__stripe" d="M700 84 C 525 94, 452 152, 400 236 C 352 316, 285 360, 160 366 C 290 352, 352 308, 404 226 C 455 146, 530 100, 700 96 Z" fill="#3b3f45"/>
    <path class="wave__stripe" d="M0 352 C 110 366, 230 364, 320 340 C 240 374, 110 374, 0 366 Z" fill="#3b3f45"/>
    <path class="wave__fill" d="M700 105 C 540 115, 470 170, 420 250 C 370 330, 300 375, 0 378 L 0 400 L 700 400 Z" fill="#1b78c2"/>
  </svg>

  <div class="wordmark">
    <span class="wordmark__square"></span>
    <span>Stonebridge Building and Projects</span>
  </div>

  <div class="person">
    <div class="person__name">Omar Haddani</div>
    <div class="person__role">Managing Director</div>
  </div>

  <ul class="contacts">
    <li>0400 123 987
      <svg width="15" height="15" viewBox="0 0 16 16"><circle cx="8" cy="8" r="7" fill="none" stroke="#fff" stroke-width="1.4"/><path d="M5.5 4.5l1.5 1.5-1 1c.6 1.2 1.4 2 2.6 2.6l1-1 1.5 1.5-1 1.1C8 11 5 8 4.6 5.6z" fill="#fff"/></svg></li>
    <li>sbp_building
      <svg width="15" height="15" viewBox="0 0 16 16"><circle cx="8" cy="8" r="6.5" fill="none" stroke="#fff" stroke-width="1.4"/></svg></li>
    <li>omar@sbpbuilding.com.au
      <svg width="15" height="15" viewBox="0 0 16 16"><rect x="1.5" y="3.5" width="13" height="9" fill="none" stroke="#fff" stroke-width="1.4"/><path d="M1.5 3.5l6.5 5 6.5-5" fill="none" stroke="#fff" stroke-width="1.4"/></svg></li>
    <li>www.sbpbuilding.com.au
      <svg width="15" height="15" viewBox="0 0 16 16"><circle cx="8" cy="8" r="6.5" fill="none" stroke="#fff" stroke-width="1.4"/><ellipse cx="8" cy="8" rx="2.8" ry="6.5" fill="none" stroke="#fff" stroke-width="1.2"/><path d="M1.5 8h13" stroke="#fff" stroke-width="1.2"/></svg></li>
  </ul>
</section>

</body>
</html>
```